Web design project for exciting Australian start-up

Background
We are looking for a creative and talented web design artist to work alongside our market leading web developer.
• You will be required to create a modern and clean design theme for our website, incorporating selected rustic colour scheme elements for our exciting Australian start-up to operate within the coffee industry.
reoccurring work to be expected to flow to the successful designer.
Requirements
• c. 5 - 10 page website
• Landing page
• Log in/ out
• 404 template
• Typography is emphasised
• Please use either a) typemarrow.com, b) free web fonts, c) brindle fonts
• All design elements in vector format
• Preferably with icons for each header title(i.e. about us, how it works etc) but designer have free reign over how the site looks, so might not be applicable
• All pages to be responsive
• Down to eSlab resolution

High level visual design brief attached - additional pages to be worked from base design.

Design inspiration
• We would like to use design elements from the following sources:
http://www.zandrix.com/halcyon/ (Functionality)
Colour scheme refer to logo and complementary style guide

```html
<!DOCTYPE html>
<html lang="en">
<head>
<meta charset="utf-8">
<title>Bean Meridian</title>
<link rel="stylesheet" href="https://fonts.googleapis.com/css2?family=Arimo:wght@400;700&family=Cabin:wght@500;700&display=swap">
<style>
:root{
  --accent:#e29a4c;
  --olive:#6b6a4c;
  --header-bg:#f1f0ef;
  --ink:#111;
  --body-text:#555;
  --footer-bg:#4a4b47;
  --footer-text:#fff;
  --footer-head:#e8a04a;
  --card-border:#c9c9c9;
  --rail-mail:#c7601a;
  --rail-2:#2a8fc0;
  --rail-3:#3c5a99;
  --rail-4:#4b6cb0;
  --rail-5:#b0242c;
  --rail-6:#7a4a3a;
  --rail-search:#333;
}
*{margin:0;padding:0;box-sizing:border-box}
html,body{width:1200px;height:1032px;overflow:hidden}
body{position:relative;background:#fff;font-family:"Arimo",Arial,sans-serif;color:var(--ink)}
.abs{position:absolute}
.top-strip{left:0;top:0;width:1200px;height:8px;background:var(--accent)}
.site-header{left:0;top:8px;width:1200px;height:104px;background:var(--header-bg)}
.header-rule{left:0;top:112px;width:1200px;height:4px;background:linear-gradient(#4a4946,#77746e)}
.brand{left:200px;top:20px;height:86px;display:flex;align-items:center;gap:12px}
.brand-mark{width:46px;height:46px;border-radius:50%;background:#2e2d2b}
.brand-name{font-family:"Arimo",sans-serif;font-weight:700;font-size:27px;letter-spacing:1px;color:#222}
.account{left:847px;top:40px;width:152px;height:35px;border:1px solid #cfcdca;background:linear-gradient(#fafafa,#e9e8e6);display:flex;align-items:center;font-weight:700;font-size:12px;color:#444}
.account a{display:flex;align-items:center;gap:6px;padding:0 7px;color:#444;text-decoration:none}
.account .sep{width:0;height:24px;border-left:1px dotted #aaa}
.hero{left:0;top:116px;width:1200px;height:466px;background:radial-gradient(ellipse at 35% 40%,#d8cfc4 0%,#9c7c60 30%,#5a3a24 60%,#3a2416 100%)}
.hero-title{left:200px;top:296px;font-family:"Cabin",sans-serif;font-weight:500;font-size:33px;line-height:40px;color:#fff;text-shadow:0 1px 3px rgba(0,0,0,.6);letter-spacing:.5px}
.watch{left:200px;top:399px;width:221px;height:51px;display:flex}
.watch-label{width:172px;background:var(--olive);color:#fff;font-size:20px;display:flex;align-items:center;padding-left:20px}
.watch-play{width:49px;background:var(--accent);display:flex;align-items:center;justify-content:center}
.intro-title{left:0;top:596px;width:1200px;text-align:center;font-weight:700;font-size:20px}
.intro-text{left:200px;top:634px;width:800px;text-align:center;font-size:11.2px;line-height:19.2px;color:var(--body-text)}
.card{top:743px;width:245px;height:80px;border:1px solid var(--card-border);background:linear-gradient(#fff,#e6e6e6);display:flex;align-items:center;font-size:20px;color:#555}
.card-icon{width:54px;height:54px;margin:0 22px 0 16px;border-radius:8px}
.card-faq{justify-content:flex-start}
.site-footer{left:0;top:860px;width:1200px;height:172px;background:var(--footer-bg);border-top:2px solid #6a6b66}
.f-head{font-weight:700;font-size:12px;color:var(--footer-head)}
.f-links{list-style:none;font-size:10px;line-height:16.5px;color:var(--footer-text)}
.tweet{font-size:10px;line-height:11.6px;color:var(--footer-text);width:180px}
.tweet b{color:#e22;font-weight:400}
.follow{display:flex;gap:4px}
.follow span{width:18px;height:18px;display:block}
.dots{top:986px;height:0;border-top:1px dotted #8d8e88}
.copyright{left:0;top:1004px;width:1200px;text-align:center;font-size:12px;color:#fff}
.rail{left:1174px;top:466px;width:26px}
.rail span{display:flex;width:26px;height:28px;align-items:center;justify-content:center}
</style>
</head>
<body>
<div class="abs top-strip"></div>
<header class="abs site-header"></header>
<div class="abs header-rule"></div>
<div class="abs brand"><span class="brand-mark"></span><span class="brand-name">BEAN MERIDIAN</span></div>
<nav class="abs account">
  <a href="#"><svg width="14" height="14" viewBox="0 0 14 14"><rect x="1" y="1" width="12" height="12" fill="none" stroke="#e29a4c" stroke-width="1.5"/><path d="M3 7h6M7 4l3 3-3 3" fill="none" stroke="#e29a4c" stroke-width="1.5"/></svg>Login</a>
  <span class="sep"></span>
  <a href="#"><svg width="14" height="14" viewBox="0 0 14 14"><rect x="1" y="1" width="12" height="12" rx="2" fill="none" stroke="#e29a4c" stroke-width="1.5"/><path d="M7 11V4M4 7l3-3 3 3" fill="none" stroke="#e29a4c" stroke-width="1.5"/></svg>Sign Up</a>
</nav>

<section class="abs hero" role="img" aria-label="Photo of a white cup of coffee on a saucer with cinnamon sticks and star anise, surrounded by coffee beans spilling from a burlap sack on a wooden table"></section>
<h1 class="abs hero-title">Australia’s first online<br>coffee&nbsp; marketplace</h1>
<a class="abs watch" href="#"><span class="watch-label">Watch Video</span><span class="watch-play"><svg width="20" height="28" viewBox="0 0 20 28"><path d="M3 2h4l11 12-11 12H3z" fill="#fff"/></svg></span></a>

<h2 class="abs intro-title">Bean Meridian</h2>
<p class="abs intro-text">Lorem ipsum dolor sit amet, consectetur adipiscing elit. Donec sit amet turpis erat. Aenean hendrerit fermentum aliquet. Nunc id nunc sapien. Suspendisse euismod dui lorem, nec fringilla arcu bibendum ac. Sed tristique augue tincidunt libero egestas, eu accumsan erat lacinia. Nullam fermentum neque urna, a mattis purus tristique eget. Quisque tempor eleifend libero, feugiat ultricies sapien posuere et. Quisque sit amet sagittis ante. Ut condimentum viverra erat, ac molestie purus euismod eu. In hac habitasse platea dictumst. Mauris nibh urna, eleifend in ligula non, euismod cursus odio. In libero purus, venenatis id</p>

<a class="abs card" style="left:199px"><span class="card-icon" role="img" aria-label="Illustration of a blue 3D bar chart" style="background:linear-gradient(#6a8fd8,#2a4fa0)"></span>How it Works</a>
<a class="abs card" style="left:475px"><span class="card-icon" role="img" aria-label="Illustration of a businessman in a blue suit" style="background:linear-gradient(#e8b088,#2a5aa8);margin-right:52px"></span>FAQ</a>
<a class="abs card" style="left:753px"><span class="card-icon" role="img" aria-label="Illustration of a blue envelope icon" style="background:linear-gradient(#7cc4f0,#2a86d0)"></span>Get Your Draft</a>

<footer class="abs site-footer"></footer>
<div class="abs f-head" style="left:200px;top:877px">Helpfull Info</div>
<ul class="abs f-links" style="left:200px;top:896px"><li>About Us</li><li>Media Enquiries</li><li>Terms &amp; Conditions</li><li>Privocy Policy</li></ul>
<div class="abs f-head" style="left:417px;top:877px">Who We Are</div>
<ul class="abs f-links" style="left:417px;top:896px"><li>How it works</li><li>FAQ</li><li>Contact Us</li></ul>
<div class="abs f-head" style="left:594px;top:874px">Tweets</div>
<p class="abs tweet" style="left:594px;top:896px"><b>RT @Kelda</b> Talking about @cratewave's values and mission at #PressForum. See the list here: http://lnk.to/rKq8Z2Wp yesterday</p>
<div class="abs f-head" style="left:894px;top:875px">Follow Us</div>
<div class="abs follow" style="left:894px;top:898px" aria-label="Social links">
  <span style="background:#4a6ab0"></span><span style="background:#3aa6d8"></span><span style="background:#c8473a"></span><span style="background:#c2364a"></span><span style="background:#f4f4f4"></span>
</div>
<div class="abs f-head" style="left:1102px;top:900px">x18</div>
<div class="abs dots" style="left:200px;width:368px"></div>
<svg class="abs" style="left:585px;top:970px" width="26" height="24" viewBox="0 0 26 24"><path d="M4 11h16v3a7 7 0 0 1-7 7h-2a7 7 0 0 1-7-7z M20 12h2a2.5 2.5 0 0 1 0 5h-2 M2 22h22 M10 3c-2 2 2 3 0 6 M14 2c-2 2 2 3 0 6" fill="none" stroke="#e29a4c" stroke-width="1.4"/></svg>
<div class="abs dots" style="left:629px;width:369px"></div>
<p class="abs copyright">Copy right@ Bean Meridian</p>

<div class="abs rail" aria-label="Share">
  <span style="background:var(--rail-mail)"><svg width="10" height="8" viewBox="0 0 10 8"><rect width="10" height="8" fill="#fff"/><path d="M0 0l5 4 5-4" fill="none" stroke="#c7601a"/></svg></span>
  <span style="background:var(--rail-2)"></span>
  <span style="background:var(--rail-3)"></span>
  <span style="background:var(--rail-4)"></span>
  <span style="background:var(--rail-5)"></span>
  <span style="background:var(--rail-6)"></span>
  <span style="background:var(--rail-search)"><svg width="10" height="10" viewBox="0 0 10 10"><circle cx="4" cy="4" r="3" fill="none" stroke="#fff" stroke-width="1.5"/><path d="M6 6l3 3" stroke="#fff" stroke-width="1.5"/></svg></span>
</div>
</body>
</html>
```